CrestHornSupply.com

I need a new webdesign for a company in the San Jose/SF Bay area that showcases the financial benefits of buying used band instruments for junior high students.This would be opposed to the current and costly option of renting cheap quality instruments from the 2 or 3 local music stores that charge a monthly fee that over the years charges the buyer 3 or 4x over..
Instruments: focus in on Alto Sax, Trumpet, Flute, Clarinet, Trombone, Tenor Sax, Baritone
Target middle schools are Larkfield Middle School and Maple Middle School in San Jose, CA. Both have award winning band programs.
Files attached may or may not be important.
Tabs Needed and funtional
Contact
Shopping Cart
Select Instrument
Checkout
Add to Cart, etc.
Instuments
quantity, etc.
trade in your instrument/sell your instrument
ability to add or take away new instruments for sale. including pictures
Additional questions or info, feel free to ask
Updates
Hi Designers,
Project Deadline Extended
Reason: In the next week you will be receiving specific content that will be required to be had on the website.
New desigins are still welcome. Please continue to contact me if you have questions about your individual designs.
Thanks!
Crest Horn

```html
<!DOCTYPE html>
<html lang="en">
<head>
<meta charset="utf-8">
<title>Crest Horn Instruments</title>
<link rel="stylesheet" href="https://fonts.googleapis.com/css2?family=Gelasio:wght@400;500&family=Open+Sans:wght@400;600;700&display=swap">
<style>
:root{
  --navy:#10306a;
  --navy-dark:#0c2656;
  --red:#c01015;
  --red-btn:#c8161b;
  --page:#f4f4f4;
  --hero:#e4e4e4;
  --ink:#333;
  --muted:#666;
  --light:#999;
  --line:#dcdcdc;
  --cart:#6fb6e4;
  --gray-btn:#6a6a6a;
  --footer-link:#b7c3dc;
}
*{box-sizing:border-box;margin:0;padding:0}
html,body{width:1036px;height:1200px;overflow:hidden}
body{background:var(--page);font-family:"Gelasio",serif;color:var(--ink);position:relative}
.abs{position:absolute}
.rainbow{top:0;left:0;width:1036px;height:3px;background:linear-gradient(90deg,#f4a7a0,#f7d58a,#a8dca0,#8fd3d6,#a7c4ef,#d2b3ea,#f4a7a0,#f7d58a,#a8dca0,#8fd3d6)}
/* header */
.brand{left:95px;top:22px}
.brand-name{font-family:"Open Sans",sans-serif;font-weight:700;font-size:28px;color:#333;line-height:32px;letter-spacing:-.5px}
.brand-sub{font-family:"Open Sans",sans-serif;font-weight:700;font-size:20px;color:#555;line-height:24px}
.util{top:16px;display:flex;align-items:center;gap:6px;font-size:10.5px;color:var(--muted);line-height:12px}
.util svg{flex:none}
.util-rule{left:589px;top:48px;width:352px;height:1px;background:var(--line)}
.account{left:588px;top:62px;display:flex;align-items:center;gap:5px;font-size:10.5px;color:var(--muted)}
.search{left:670px;top:60px;width:156px;height:22px;background:#fff;border:1px solid var(--line);font-size:10.5px;color:var(--muted);padding:4px 10px}
.search svg{position:absolute;right:7px;top:4px}
.cart{left:830px;top:60px;width:111px;height:22px;background:var(--cart);display:flex;align-items:center;font-size:11px;color:var(--navy)}
.cart .cart-ic{width:30px;height:22px;background:#4ea2d8;display:flex;align-items:center;justify-content:center;margin-right:5px}
/* nav */
.nav{top:105px;left:0;width:1036px;height:29px;background:var(--navy)}
.nav ul{list-style:none;display:flex;position:absolute;left:95px;top:0;height:29px;align-items:center}
.nav li{font-size:11.5px;color:#fff;padding:0 9px;border-left:1px solid #3a5487;line-height:12px}
.nav li:first-child{padding-left:0;border-left:none}
/* hero */
.hero{top:134px;left:0;width:1036px;height:303px;background:var(--hero)}
.hero-art{left:580px;top:150px;width:366px;height:270px;border-radius:50%;background:radial-gradient(ellipse at 55% 50%,#f1d989 0%,#d9b24b 30%,rgba(228,228,228,0) 70%)}
.hero-title{left:96px;top:224px;font-size:24px;color:var(--navy);letter-spacing:.3px}
.hero-text{left:99px;top:257px;width:240px;font-family:"Open Sans",sans-serif;font-size:12px;line-height:17px;color:#444}
.btn-details{left:100px;top:306px;width:102px;height:31px;background:var(--red-btn);color:#fff;font-size:14px;display:flex;align-items:center;justify-content:center;border-radius:2px}
.dots{left:99px;top:405px;display:flex;gap:3px}
.dots span{width:9px;height:9px;border-radius:50%;background:#aaa}
.dots span:first-child{background:var(--navy)}
/* feature band */
.features{top:437px;left:0;width:1036px;height:83px;background:var(--red)}
.feature{top:451px;display:flex;gap:14px}
.feature .circ{width:55px;height:55px;border-radius:50%;background:#fff;display:flex;align-items:center;justify-content:center;flex:none}
.feature h3{font-weight:400;font-size:15.5px;color:#fff;margin-top:5px;line-height:18px}
.feature p{font-family:"Open Sans",sans-serif;font-size:9.8px;color:#f5d0d0;line-height:16.5px;margin-top:3px;width:200px}
/* sections */
.section-title{font-size:16px;color:#444;letter-spacing:.2px}
.arrows{display:flex;gap:4px}
.card{top:566px;width:201px;height:217px;background:#fff;border:1px solid var(--line)}
.card .img{position:absolute;left:25px;top:20px;width:150px;height:110px}
.card .name{position:absolute;left:13px;top:146px;font-size:13px;color:#444}
.card .price{position:absolute;right:14px;top:146px;font-size:13px;color:var(--red)}
.card .btn{position:absolute;top:173px;width:79px;height:24px;font-family:"Open Sans",sans-serif;font-size:10.5px;color:#fff;display:flex;align-items:center;justify-content:center;font-weight:600}
.card .view{left:12px;background:var(--navy)}
.card .add{left:106px;background:linear-gradient(#7a7a7a,#5a5a5a)}
.testi{top:828px;width:414px;height:126px;background:#fff;border:1px solid var(--line)}
.testi .quote{position:absolute;left:8px;top:8px}
.testi p{position:absolute;left:25px;top:30px;width:380px;font-size:11.2px;line-height:20px;color:#555}
.testi .tail{position:absolute;left:22px;bottom:-7px;width:12px;height:12px;background:#fff;border-right:1px solid var(--line);border-bottom:1px solid var(--line);transform:rotate(45deg)}
.author{top:962px;display:flex;align-items:center;gap:8px;font-size:11.5px;color:var(--light)}
.author .av{width:49px;height:49px;border-radius:50%;background:#fff;border:1px solid var(--line);display:flex;align-items:center;justify-content:center}
/* footer */
.footer{top:1021px;left:0;width:1036px;height:120px;background:var(--navy)}
.fcol{top:1036px}
.fcol h4{font-weight:400;font-size:11.5px;color:#fff;margin-bottom:7px;letter-spacing:.2px}
.fcol ul{list-style:none}
.fcol li{font-size:11px;color:var(--footer-link);line-height:17.5px}
.field{width:138px;height:20px;background:#fff;font-size:8.5px;color:#777;padding:5px 7px;margin-bottom:5px}
.subscribe{left:695px;top:1113px;width:80px;height:20px;background:#2f62b8;color:#fff;font-size:10.5px;display:flex;align-items:center;justify-content:center}
.social{display:flex;align-items:center;gap:10px;font-size:11.5px;color:var(--footer-link);margin-bottom:8px}
.social span.c{width:26px;height:26px;border-radius:50%;background:#fff;display:block}
.bottom{top:1141px;left:0;width:1036px;height:59px;background:var(--navy-dark)}
.paybox{left:97px;top:1151px;width:208px;height:38px;background:#fff;border:2px solid #cfd6e6;display:flex;align-items:center;gap:4px;padding:0 6px}
.paybox span{width:23px;height:16px;border-radius:2px;background:#b8bfcc}
.paybox .word{margin-left:8px;font-size:15px;color:var(--navy);width:auto;height:auto;background:none}
.paynote{left:316px;top:1155px;font-size:11px;color:#c9d2e6;line-height:18px}
.copy{left:690px;top:1172px;font-size:11px;color:#c9d2e6}
</style>
</head>
<body>
<div class="abs rainbow"></div>

<header>
  <div class="abs brand">
    <div class="brand-name">Crest Horn</div>
    <div class="brand-sub">Instruments</div>
  </div>
  <div class="abs util" style="left:669px">
    <svg width="18" height="18" viewBox="0 0 18 18"><circle cx="9" cy="9" r="9" fill="#777"/><rect x="4" y="6" width="6" height="5" fill="#fff"/><path d="M10 7.5h2.5l1.5 2v1.5H10z" fill="#fff"/><circle cx="6" cy="12" r="1.2" fill="#fff"/><circle cx="12" cy="12" r="1.2" fill="#fff"/></svg>
    <span>Shipping</span>
  </div>
  <div class="abs util" style="left:749px">
    <svg width="18" height="18" viewBox="0 0 18 18"><circle cx="9" cy="9" r="9" fill="#777"/><path d="M4.5 8c1-2.5 8-2.5 9 0l-1.5 1-1-1.2h-4L6 9z" fill="#fff"/><rect x="6" y="9.5" width="6" height="3.5" rx="1" fill="#fff"/></svg>
    <span>Customer Hotline<br>1-408-555-0147</span>
  </div>
  <div class="abs util" style="left:873px">
    <svg width="18" height="18" viewBox="0 0 18 18"><circle cx="9" cy="9" r="9" fill="#777"/><path d="M9 4a3.3 3.3 0 0 0-3.3 3.3C5.7 10 9 14 9 14s3.3-4 3.3-6.7A3.3 3.3 0 0 0 9 4z" fill="#fff"/><circle cx="9" cy="7.3" r="1.2" fill="#777"/></svg>
    <span>Store<br>Locations</span>
  </div>
  <div class="abs util-rule"></div>
  <div class="abs account">
    <svg width="15" height="15" viewBox="0 0 15 15"><circle cx="7.5" cy="7.5" r="7" fill="none" stroke="#888"/><circle cx="7.5" cy="6" r="2.5" fill="none" stroke="#888"/><path d="M3.3 12.3c1-2 7.4-2 8.4 0" fill="none" stroke="#888"/></svg>
    <span>My Account</span>
  </div>
  <div class="abs search">Search
    <svg width="13" height="13" viewBox="0 0 13 13"><circle cx="5.5" cy="5.5" r="4.2" fill="none" stroke="#666" stroke-width="1.5"/><path d="M8.6 8.6l3.5 3.5" stroke="#666" stroke-width="1.6"/></svg>
  </div>
  <div class="abs cart">
    <span class="cart-ic"><svg width="18" height="15" viewBox="0 0 18 15"><path d="M1 1h3l2 9h9l2-6H5" fill="none" stroke="#10306a" stroke-width="1.6"/><circle cx="7" cy="13" r="1.3" fill="#10306a"/><circle cx="14" cy="13" r="1.3" fill="#10306a"/></svg></span>
    <span>0 items: $0.00</span>
  </div>
</header>

<nav class="abs nav">
  <ul>
    <li>HOME</li><li>ABOUT US</li><li>PRODUCTS</li><li>SALE</li><li>SELECT INSTRUMENT</li><li>INSTUMENTS</li><li>QUANTITY</li><li>CONTACT US</li>
  </ul>
</nav>

<section class="abs hero">
</section>
<div class="abs hero-art" role="img" aria-label="Two brass trumpets, polished gold finish"></div>
<h1 class="abs hero-title" style="font-weight:400">BAND INSTRUMENTS</h1>
<p class="abs hero-text">Lorem Ipsum is simply dummy text of the printing and typesetting industry</p>
<div class="abs btn-details">DETAILS</div>
<div class="abs dots"><span></span><span></span><span></span></div>

<section class="abs features"></section>
<div class="abs feature" style="left:96px">
  <div class="circ"><svg width="24" height="24" viewBox="0 0 24 24"><path d="M3 12l6 7L21 4" fill="none" stroke="#c01015" stroke-width="3.5" stroke-linecap="round" stroke-linejoin="round"/></svg></div>
  <div><h3>CUSTOMER SATISFACTION</h3><p>Lorem Ipsum is simply dummy text of the printing and typesetting industry</p></div>
</div>
<div class="abs feature" style="left:395px">
  <div class="circ"><svg width="28" height="28" viewBox="0 0 28 28"><path d="M15 3h10v10L13 25 3 15z" fill="#c01015"/><circle cx="20" cy="8" r="2" fill="#fff"/></svg></div>
  <div><h3>PRODUCTS</h3><p>Lorem Ipsum is simply dummy text of the printing and typesetting industry</p></div>
</div>
<div class="abs feature" style="left:680px">
  <div class="circ"><svg width="30" height="26" viewBox="0 0 30 26"><ellipse cx="15" cy="11" rx="12.5" ry="8.5" fill="none" stroke="#c01015" stroke-width="2.4"/><path d="M8 18l-3 6 8-4" fill="none" stroke="#c01015" stroke-width="2.4" stroke-linejoin="round"/></svg></div>
  <div><h3>FEEDBACK</h3><p>Lorem Ipsum is simply dummy text of the printing and typesetting industry</p></div>
</div>

<h2 class="abs section-title" style="left:95px;top:534px;font-weight:400">PRODUCTS</h2>
<div class="abs arrows" style="left:917px;top:535px">
  <svg width="11" height="16" viewBox="0 0 11 16"><path d="M9 1L2 8l7 7" fill="none" stroke="#888" stroke-width="1.4"/></svg>
  <svg width="11" height="16" viewBox="0 0 11 16"><path d="M2 1l7 7-7 7" fill="none" stroke="#888" stroke-width="1.4"/></svg>
</div>

<article class="abs card" style="left:95px">
  <div class="img" role="img" aria-label="Alto saxophone, brass" style="background:radial-gradient(ellipse at 50% 50%,#d8c07a 0%,#eee2b8 35%,#fff 70%)"></div>
  <div class="name">ALTO SAX</div><div class="price">$20,00</div>
  <div class="btn view">View Detail</div><div class="btn add">Add to Cart</div>
</article>
<article class="abs card" style="left:310px">
  <div class="img" role="img" aria-label="Trumpet, brass" style="background:radial-gradient(ellipse at 50% 50%,#e0c26a 0%,#f1e3b6 35%,#fff 70%)"></div>
  <div class="name">TRUMPET</div><div class="price">$20,00</div>
  <div class="btn view">View Detail</div><div class="btn add">Add to Cart</div>
</article>
<article class="abs card" style="left:525px">
  <div class="img" role="img" aria-label="Wooden flute" style="background:radial-gradient(ellipse at 50% 50%,#c98a4a 0%,#ecd2b4 30%,#fff 65%)"></div>
  <div class="name">FLUTE</div><div class="price">$20,00</div>
  <div class="btn view">View Detail</div><div class="btn add">Add to Cart</div>
</article>
<article class="abs card" style="left:740px">
  <div class="img" role="img" aria-label="Black clarinet with silver keys" style="background:radial-gradient(ellipse at 50% 50%,#444 0%,#bdbdbd 30%,#fff 65%)"></div>
  <div class="name">CLARINET</div><div class="price">$20,00</div>
  <div class="btn view">View Detail</div><div class="btn add">Add to Cart</div>
</article>

<h2 class="abs section-title" style="left:95px;top:799px;font-weight:400">CUSTOMER TESTIMONIALS</h2>
<div class="abs arrows" style="left:917px;top:801px">
  <svg width="11" height="16" viewBox="0 0 11 16"><path d="M9 1L2 8l7 7" fill="none" stroke="#888" stroke-width="1.4"/></svg>
  <svg width="11" height="16" viewBox="0 0 11 16"><path d="M2 1l7 7-7 7" fill="none" stroke="#888" stroke-width="1.4"/></svg>
</div>

<blockquote class="abs testi" style="left:95px">
  <svg class="quote" width="44" height="34" viewBox="0 0 44 34"><path d="M2 32V20C2 10 7 4 16 2l1 4c-5 2-7 5-7 9h7v17zM24 32V20c0-10 5-16 14-18l1 4c-5 2-7 5-7 9h7v17z" fill="#e2e2e2"/></svg>
  <p>Lorem Ipsum is simply dummy text of the printing and &nbsp;typesetting industry. Lorem Ipsum has been the industry's standard dummy text ever since the 1500s, when an unknown printer took a galley of type and scrambled it to make a type specimen book.</p>
  <span class="tail"></span>
</blockquote>
<blockquote class="abs testi" style="left:526px">
  <svg class="quote" width="44" height="34" viewBox="0 0 44 34" style="top:14px"><path d="M2 32V20C2 10 7 4 16 2l1 4c-5 2-7 5-7 9h7v17zM24 32V20c0-10 5-16 14-18l1 4c-5 2-7 5-7 9h7v17z" fill="#e2e2e2"/></svg>
  <p style="top:35px">Lorem Ipsum is simply dummy text of the printing and &nbsp;typesetting industry. Lorem Ipsum has been the industry's standard dummy text ever since the 1500s, when an unknown printer took a galley of type and scrambled it to make a type specimen book.</p>
  <span class="tail"></span>
</blockquote>
<div class="abs author" style="left:97px">
  <span class="av"><svg width="22" height="24" viewBox="0 0 22 24"><circle cx="11" cy="7" r="6" fill="#bbb"/><path d="M0 24c0-7 5-10 11-10s11 3 11 10z" fill="#bbb"/></svg></span>Mara Quinn
</div>
<div class="abs author" style="left:529px">
  <span class="av"><svg width="22" height="24" viewBox="0 0 22 24"><circle cx="11" cy="7" r="6" fill="#bbb"/><path d="M0 24c0-7 5-10 11-10s11 3 11 10z" fill="#bbb"/></svg></span>Mara Quinn
</div>

<footer>
  <div class="abs footer"></div>
  <div class="abs fcol" style="left:97px">
    <h4>VIEW ALL OF OUR PRODUCTS</h4>
    <div style="display:flex;gap:45px">
      <ul><li>Alto Sax</li><li>Trumpet</li><li>Flute</li><li>Clarinet</li></ul>
      <ul><li>Trombone</li><li>Tenor Sax</li><li>Baritone</li></ul>
    </div>
  </div>
  <div class="abs fcol" style="left:321px">
    <h4>YOUR ACCOUNT</h4>
    <ul><li>Sign In</li><li>Your Basket (0)</li><li>Checkout</li><li>Register</li></ul>
  </div>
  <div class="abs fcol" style="left:475px">
    <h4>LET US HELP</h4>
    <ul><li>Contact Us</li><li>Terms &amp; Conditions</li><li>Returns &amp; Shipping</li><li>About Us</li></ul>
  </div>
  <div class="abs fcol" style="left:636px">
    <h4>JOIN OUR MAILING LIST</h4>
    <div class="field">Name</div>
    <div class="field">Email Address</div>
  </div>
  <div class="abs subscribe">SUBSCRIBE</div>
  <div class="abs fcol" style="left:835px">
    <h4>FOLLOW US</h4>
    <div class="social"><span class="c"></span>Friendpage</div>
    <div class="social"><span class="c"></span>Chirper</div>
  </div>

  <div class="abs bottom"></div>
  <div class="abs paybox"><span></span><span></span><span></span><span></span><span></span><span class="word">PayWell</span></div>
  <p class="abs paynote">We accept Vantix, Meridian payments.<br>We also take payments from customers with a PayWell account.</p>
  <p class="abs copy">Copyright © 2014 CrestHorn. All Rights Reserved.</p>
</footer>
</body>
</html>
```